New Business card design to reflect rebrand

I would like a business card design with a good base colour for our new logo and also a placeholder for a profile pic of the card holder. the design needs to be editable to the point that we can easily change the picture of the person and use that design for printmerlo etc. we are looking at a metalic finish business card so will need a good base colour to bring out the finish.

Target Market(s)

prospective customers

Industry/Entity Type

Business

Contact Information for Business Card

I would like one editable design that we can change the name of the card holder and profile picture. The design need to be in a format that be send to printmerlo etc.

Our address is Fenwick Lodge, Copse Lane, Ellbrook Marsh, GU14 3TP Tel no. 01483 556172

Requirements
Must have
• place holder for a profile pic for the card holder. in AI or preferably PSD format

```html
<!DOCTYPE html>
<html lang="en">
<head>
<meta charset="utf-8">
<title>Corvane Workplace Services – Business Card</title>
<link rel="stylesheet" href="https://fonts.googleapis.com/css2?family=Open+Sans:wght@400;600;700&display=swap">
<style>
  :root {
    --page: #e9e7e3;
    --metal-light: #f4f5f6;
    --metal-mid: #c9cbce;
    --metal-dark: #9fa2a6;
    --ink: #111213;
    --ink-soft: #2a2b2d;
    --band: #0d0d0e;
    --band-text: #ffffff;
    --photo-light: #8a8c8f;
    --photo-dark: #4a4b4d;
  }
  * { margin: 0; padding: 0; box-sizing: border-box; }
  html, body {
    width: 1200px; height: 843px; overflow: hidden;
    background: var(--page);
    font-family: "Open Sans", Arial, sans-serif;
  }
  .sheet {
    width: 1200px; height: 843px;
    display: flex; flex-direction: column; align-items: center; justify-content: center;
    gap: 40px;
  }
  .card {
    position: relative;
    width: 640px; height: 366px;
    overflow: hidden;
    background:
      repeating-linear-gradient(0deg, rgba(255,255,255,0.18) 0 1px, rgba(0,0,0,0.035) 1px 3px, rgba(255,255,255,0.08) 3px 5px),
      linear-gradient(160deg, var(--metal-mid) 0%, var(--metal-light) 35%, var(--metal-mid) 60%, var(--metal-light) 78%, var(--metal-dark) 100%);
    box-shadow: 0 6px 18px rgba(0,0,0,0.25);
  }

  /* Back */
  .card-back .brand {
    position: absolute; left: 0; right: 0; top: 120px;
    text-align: center;
    font-weight: 700; font-size: 64px; letter-spacing: 4px;
    color: var(--ink);
  }
  .card-back .web {
    position: absolute; left: 0; right: 0; top: 212px;
    text-align: center;
    font-size: 17px; letter-spacing: 9px;
    color: var(--ink-soft);
  }

  /* Front */
  .card-front .brand {
    position: absolute; left: 150px; top: 34px; width: 300px;
    text-align: center;
    font-weight: 700; color: var(--ink);
    line-height: 1.05;
  }
  .brand .name { display: block; font-size: 44px; letter-spacing: 3px; }
  .brand .sub { display: block; font-size: 15px; letter-spacing: 3.5px; }
  .contact {
    position: absolute; left: 40px; top: 150px;
    font-size: 15px; line-height: 21px; color: var(--ink-soft);
    list-style: none;
  }
  .contact .phone { display: flex; align-items: center; gap: 8px; margin-top: 4px; }
  .contact svg { width: 12px; height: 12px; fill: var(--ink); }
  .profile-photo {
    position: absolute; right: 40px; top: 110px;
    width: 230px; height: 256px;
    background: linear-gradient(180deg, var(--photo-light) 0%, var(--photo-dark) 100%);
    opacity: 0.85;
  }
  .name-band { position: absolute; left: 0; bottom: 0; width: 640px; height: 70px; }
  .holder {
    position: absolute; right: 24px; bottom: 14px;
    color: var(--band-text); font-size: 20px;
  }
  .holder strong { font-weight: 700; }
  .holder span { font-size: 15px; }
</style>
</head>
<body>
<main class="sheet">
  <section class="card card-back">
    <div class="brand">CORVANE</div>
    <div class="web">WWW.CORVANE.COM</div>
  </section>

  <section class="card card-front">
    <div class="brand">
      <span class="name">CORVANE</span>
      <span class="sub">WORKPLACE SERVICES</span>
    </div>
    <ul class="contact">
      <li>Fenwick Lodge</li>
      <li>Copse Lane, Ellbrook Marsh</li>
      <li>GU14 3TP</li>
      <li class="phone">
        <svg viewBox="0 0 24 24" aria-hidden="true"><path d="M6.6 10.8a15.1 15.1 0 0 0 6.6 6.6l2.2-2.2a1 1 0 0 1 1-.25 11.4 11.4 0 0 0 3.6.57 1 1 0 0 1 1 1V20a1 1 0 0 1-1 1A17 17 0 0 1 3 4a1 1 0 0 1 1-1h3.5a1 1 0 0 1 1 1c0 1.25.2 2.45.57 3.6a1 1 0 0 1-.25 1z"/></svg>
        01483 556172
      </li>
    </ul>
    <div class="profile-photo" role="img" aria-label="Profile photo of the card holder"></div>
    <svg class="name-band" viewBox="0 0 640 70" preserveAspectRatio="none" aria-hidden="true">
      <polygon points="300,28 640,0 640,70 272,70" fill="#0d0d0e"/>
    </svg>
    <div class="holder"><strong>Daniel Hart</strong> <span>- CEO/Founder</span></div>
  </section>
</main>
</body>
</html>
```